New stationary design for online film company

We need some new stationary to fit with our new logo. The stationary should be professional, clean and simple.
We need designs for a full set of business stationary.
We need - letterhead, envelopes, invoices, proposals, coverslip/note and cover page

Industry/Entity Type

Business

```html
<!DOCTYPE html>
<html lang="en">
<head>
<meta charset="utf-8">
<title>Northreel stationery set</title>
<link rel="stylesheet" href="https://fonts.googleapis.com/css2?family=Mulish:wght@400;600;700;800&display=swap">
<style>
  :root {
    --navy: #0f4a75;
    --sky: #6fa6c3;
    --paper: #ffffff;
    --paper-shade: #f2f2f2;
    --ink: #4a4a4a;
    --faint: #e4e6ee;
    --backdrop: #e8e3dc;
    --label: #ffffff;
    --label-bg: #b98a5e;
  }
  * { box-sizing: border-box; margin: 0; padding: 0; }
  html, body { width: 1200px; height: 483px; overflow: hidden; }
  body {
    position: relative;
    background: var(--backdrop);
    font-family: "Mulish", Arial, sans-serif;
    color: var(--ink);
  }
  .sheet {
    position: absolute;
    background: linear-gradient(135deg, var(--paper) 0%, var(--paper-shade) 100%);
    box-shadow: 0 2px 6px rgba(0,0,0,.18);
    overflow: hidden;
  }
  .brand {
    position: absolute;
    display: flex;
    align-items: center;
    gap: 5px;
    color: var(--navy);
    font-weight: 700;
    letter-spacing: -0.5px;
    white-space: nowrap;
  }
  .brand-dot {
    display: inline-block;
    border-radius: 50%;
    background: var(--navy);
  }
  .small-print { position: absolute; font-size: 5.5px; color: var(--ink); white-space: nowrap; }
  .wave { position: absolute; left: 0; bottom: 0; width: 100%; }

  /* letterhead option 1 */
  .letterhead-one { left: 8px; top: 14px; width: 333px; height: 431px; }
  .letterhead-one .brand { left: 100px; top: 14px; font-size: 23px; }
  .letterhead-one .brand-dot { width: 22px; height: 22px; }
  .faint-circle {
    position: absolute; left: 88px; top: 140px; width: 175px; height: 175px;
    border-radius: 50%; background: var(--faint);
  }
  .letterhead-one .small-print { left: 40px; bottom: 8px; }

  /* letterhead option 2 */
  .letterhead-two { left: 374px; top: 14px; width: 333px; height: 431px; }
  .letterhead-two .brand { left: 12px; top: 16px; font-size: 23px; }
  .letterhead-two .brand-dot { width: 22px; height: 22px; }
  .letterhead-two .address { left: 258px; top: 24px; border-left: 1px solid #bbb; padding-left: 3px; line-height: 7px; }
  .letterhead-two .contacts { right: 14px; bottom: 10px; color: #fff; text-align: right; line-height: 8px; }

  .option-label {
    position: absolute; top: 459px; font-size: 21px; font-weight: 400; color: var(--label);
    text-shadow: 0 0 3px rgba(0,0,0,.35);
  }
  .label-one { left: 117px; }
  .label-two { left: 482px; }
  .option-label { background: var(--label-bg); padding: 0 8px; border-radius: 2px; line-height: 24px; }

  /* envelopes */
  .envelope-back { left: 820px; top: 0; width: 380px; height: 167px; }
  .envelope-back .flap { position: absolute; left: 0; top: 0; width: 100%; height: 66px; }
  .envelope-back .flap-dot {
    position: absolute; left: 175px; top: 14px; width: 30px; height: 30px;
    border-radius: 50%; background: var(--paper);
  }
  .envelope-middle { left: 740px; top: 73px; width: 372px; height: 165px; }
  .envelope-middle .flap { position: absolute; left: 0; top: 0; width: 100%; height: 78px; }
  .envelope-middle .flap-dot {
    position: absolute; left: 171px; top: 26px; width: 30px; height: 30px;
    border-radius: 50%; background: var(--navy);
  }
  .envelope-front { left: 780px; top: 146px; width: 372px; height: 167px; }
  .envelope-front .brand { left: 10px; top: 14px; font-size: 19px; }
  .envelope-front .brand-dot { width: 18px; height: 18px; }
  .envelope-front .address { left: 34px; top: 45px; }
  .envelope-front .web { right: 12px; bottom: 15px; color: #fff; font-size: 6.5px; letter-spacing: 1.5px; }

  /* business cards */
  .card-front { left: 770px; top: 342px; width: 186px; height: 106px; }
  .card-front .brand { left: 13px; top: 10px; font-size: 17px; }
  .card-front .brand-dot { width: 16px; height: 16px; }
  .card-front .holder { position: absolute; left: 13px; top: 58px; }
  .holder-name { font-size: 7.5px; font-weight: 800; color: var(--navy); }
  .holder-title { font-size: 5.5px; color: var(--sky); }
  .card-front .contacts { right: 7px; top: 63px; text-align: right; line-height: 7px; font-size: 4.8px; }
  .card-front .address { right: 7px; bottom: 4px; color: #fff; font-size: 4.8px; }
  .card-back { left: 973px; top: 341px; width: 167px; height: 107px; background: var(--navy); }
  .card-back .back-dot {
    position: absolute; left: 63px; top: 20px; width: 41px; height: 41px;
    border-radius: 50%; background: var(--paper);
  }
  .card-back .web { left: 0; width: 100%; text-align: center; top: 90px; color: #fff; font-size: 6px; letter-spacing: 1.2px; }
</style>
</head>
<body>

  <section class="sheet letterhead-one" aria-label="Letterhead option 1">
    <div class="brand"><span class="brand-dot"></span>northreel</div>
    <div class="faint-circle"></div>
    <p class="small-print">Street Name, City Name, State Zip Code &nbsp;|&nbsp; ✆ 123-456-0789 &nbsp; ✉ info@northreel.com &nbsp; ◉ www.northreel.com</p>
  </section>

  <section class="sheet letterhead-two" aria-label="Letterhead option 2">
    <div class="brand"><span class="brand-dot"></span>northreel</div>
    <p class="small-print address">Street Name, City Name<br>State Zip Code</p>
    <svg class="wave" viewBox="0 0 333 52" height="52" preserveAspectRatio="none">
      <path d="M0 34 C110 12 220 2 333 0 L333 6 C220 8 110 20 0 40 Z" fill="var(--sky)"/>
      <path d="M0 44 C110 24 220 14 333 11 L333 52 L0 52 Z" fill="var(--navy)"/>
    </svg>
    <p class="small-print contacts">✆ 123-456-0789<br>✉ info@northreel.com<br>◉ www.northreel.com</p>
  </section>

  <p class="option-label label-one">Option-1</p>
  <p class="option-label label-two">Option-2</p>

  <section class="sheet envelope-back" aria-label="Envelope back">
    <svg class="flap" viewBox="0 0 380 66" preserveAspectRatio="none">
      <path d="M0 0 H380 V22 L205 64 Q190 67 175 64 L0 22 Z" fill="var(--navy)"/>
    </svg>
    <span class="flap-dot"></span>
  </section>

  <section class="sheet envelope-middle" aria-label="Envelope back, white flap">
    <svg class="flap" viewBox="0 0 372 78" preserveAspectRatio="none">
      <path d="M0 0 L186 74 L372 0" fill="none" stroke="#555" stroke-width="0.8"/>
    </svg>
    <span class="flap-dot"></span>
  </section>

  <section class="sheet envelope-front" aria-label="Envelope front">
    <div class="brand"><span class="brand-dot"></span>northreel</div>
    <p class="small-print address">Street Name, City Name, State Zip Code</p>
    <svg class="wave" viewBox="0 0 372 50" height="50" preserveAspectRatio="none">
      <path d="M0 32 C120 16 250 2 372 0 L372 6 C250 8 120 22 0 38 Z" fill="var(--sky)"/>
      <path d="M0 42 C120 26 250 13 372 11 L372 50 L0 50 Z" fill="var(--navy)"/>
    </svg>
    <p class="small-print web">www.northreel.com</p>
  </section>

  <section class="sheet card-front" aria-label="Business card front">
    <div class="brand"><span class="brand-dot"></span>northreel</div>
    <div class="holder">
      <p class="holder-name">Your Name</p>
      <p class="holder-title">Title</p>
    </div>
    <svg class="wave" viewBox="0 0 186 62" height="62" preserveAspectRatio="none">
      <path d="M0 38 C60 20 120 6 186 4 L186 9 C120 11 60 24 0 43 Z" fill="var(--sky)"/>
      <path d="M0 48 C60 30 120 18 186 15 L186 62 L0 62 Z" fill="var(--navy)"/>
    </svg>
    <p class="small-print contacts">✆ 123-456-0789<br>✆ 123-456-0789<br>✉ info@northreel.com<br>◉ www.northreel.com</p>
    <p class="small-print address">Street Name, City Name, State Zip Code</p>
  </section>

  <section class="sheet card-back" aria-label="Business card back">
    <span class="back-dot"></span>
    <p class="small-print web">www.northreel.com</p>
  </section>

</body>
</html>
```